Business Card and Letterhead for Pimlu - modern real estate business

I need a double sided business card design for Pimlu. Please see business card brief here https://files.trelvonadocs.com/sheet/r/7QzTmWbaXLJnoPEd-kRyUgFhHsstbvCe2qfoMxDa_pz/view?mode=shared

Please feel free to design the business cards however you feel best. I am happy to give some creative freedoms and then provide feedback from there.

Please then also create a letterhead to match the business card design

Colors

Designer to choose colors to be used in the design.

Requirements
Must have
• Must be a modern, elegant business card which looks very professional

```html
<!DOCTYPE html>
<html lang="en">
<head>
<meta charset="utf-8">
<title>Pimlu Business Card</title>
<link href="https://fonts.googleapis.com/css2?family=Roboto:wght@400;500;700&display=swap" rel="stylesheet">
<style>
  :root {
    --stage: #e6e6e6;
    --card: #2b2b2c;
    --band-dark: #222223;
    --band-mid: #2f2f30;
    --red: #e31b23;
    --white: #f4f4f4;
    --photo-a: #6f7a6a;
    --photo-b: #3a3530;
  }
  * { box-sizing: border-box; margin: 0; padding: 0; }
  html, body { width: 1200px; height: 960px; overflow: hidden; }
  body {
    background: var(--stage);
    font-family: "Roboto", Arial, sans-serif;
    position: relative;
  }
  .card {
    position: absolute;
    left: 250px;
    width: 700px;
    height: 400px;
    background: var(--card);
    overflow: hidden;
    box-shadow: 0 6px 18px rgba(0,0,0,.25);
  }
  .card--front { top: 60px; }
  .card--back { top: 500px; }

  /* front */
  .front-band-top, .front-band-bottom {
    position: absolute; left: 0; width: 100%; background: var(--band-dark);
  }
  .front-band-top { top: 0; height: 90px; }
  .front-band-bottom { bottom: 0; height: 90px; }
  .front-band-mid {
    position: absolute; top: 90px; left: 0; width: 100%; height: 220px;
    background: var(--band-mid);
    display: flex; align-items: center; justify-content: center;
  }
  .brand-name {
    color: var(--red);
    font-weight: 700;
    letter-spacing: 6px;
    line-height: 1;
  }
  .front-band-mid .brand-name { font-size: 112px; }

  /* back */
  .back-band {
    position: absolute; top: 50px; left: 200px; right: 0; height: 110px;
    background: var(--band-dark);
    display: flex; align-items: center; justify-content: flex-end;
    padding-right: 40px;
  }
  .back-band .brand-name { font-size: 72px; letter-spacing: 4px; }
  .portrait {
    position: absolute; left: 55px; top: 55px;
    width: 200px; height: 200px; border-radius: 50%;
    border: 6px solid var(--red);
    background: radial-gradient(circle at 55% 45%, var(--photo-a), var(--photo-b));
  }
  .agent {
    position: absolute; left: 60px; top: 278px;
    color: var(--white); font-size: 16px; line-height: 1.35;
  }
  .agent-name { color: var(--red); font-size: 26px; font-weight: 500; margin-bottom: 2px; }
  .label { color: var(--red); }
  .contact-line { display: flex; align-items: center; gap: 10px; }
  .contact-line svg { width: 14px; height: 14px; flex: none; fill: var(--red); }
  .office {
    position: absolute; right: 40px; top: 190px;
    color: var(--white); font-size: 16px; line-height: 1.35; text-align: right;
  }
  .office .contact-line { justify-content: flex-end; flex-direction: row-reverse; }
  .office-gap { height: 14px; }
</style>
</head>
<body>

<section class="card card--front">
  <div class="front-band-top"></div>
  <div class="front-band-mid"><span class="brand-name">PIMLU</span></div>
  <div class="front-band-bottom"></div>
</section>

<section class="card card--back">
  <div class="back-band"><span class="brand-name">PIMLU</span></div>
  <div class="portrait" role="img" aria-label="Portrait photo of the agent"></div>

  <div class="agent">
    <div class="agent-name">Dane Corrow</div>
    <div>Licenced Real Estate Agent</div>
    <div><span class="label">Lic No.</span> 20317492</div>
    <div class="contact-line">
      <svg viewBox="0 0 24 24"><path d="M6.6 10.8a15.1 15.1 0 0 0 6.6 6.6l2.2-2.2a1 1 0 0 1 1-.25 11.4 11.4 0 0 0 3.6.57 1 1 0 0 1 1 1V20a1 1 0 0 1-1 1A17 17 0 0 1 3 4a1 1 0 0 1 1-1h3.5a1 1 0 0 1 1 1c0 1.25.2 2.45.57 3.57a1 1 0 0 1-.25 1z"/></svg>
      <span>+61 400 218 547</span>
    </div>
    <div class="contact-line">
      <svg viewBox="0 0 24 24"><path d="M2 5h20v14H2zm2 2v.5l8 5 8-5V7l-8 5z"/></svg>
      <span>ceo@brightquillagency.com</span>
    </div>
  </div>

  <div class="office">
    <div><span class="label">Lic No.</span> 10048213</div>
    <div>PO Box 3170</div>
    <div>Larkfield NSW 2790</div>
    <div class="office-gap"></div>
    <div class="contact-line">
      <svg viewBox="0 0 24 24"><path d="M6.6 10.8a15.1 15.1 0 0 0 6.6 6.6l2.2-2.2a1 1 0 0 1 1-.25 11.4 11.4 0 0 0 3.6.57 1 1 0 0 1 1 1V20a1 1 0 0 1-1 1A17 17 0 0 1 3 4a1 1 0 0 1 1-1h3.5a1 1 0 0 1 1 1c0 1.25.2 2.45.57 3.57a1 1 0 0 1-.25 1z"/></svg>
      <span>02 4610 3395</span>
    </div>
    <div class="contact-line">
      <svg viewBox="0 0 24 24"><path d="M2 5h20v14H2zm2 2v.5l8 5 8-5V7l-8 5z"/></svg>
      <span>info@pimlu.com</span>
    </div>
    <div class="contact-line">
      <svg viewBox="0 0 24 24"><circle cx="12" cy="12" r="10"/></svg>
      <span>www.<span class="label">pimlu</span>.com</span>
    </div>
  </div>
</section>

</body>
</html>
```